Harborline Auto LLC

Car Dealer Customer Service
Address: 2874 Cresthaven Road, Marlowe Bend, OR 97418
web: www.harborlineautoxq.net
email: harborlineautoxq@mailnest.example
Phone: (503) 555-0148
Phone: (971) 555-0173

```html
<!DOCTYPE html>
<html lang="en">
<head>
<meta charset="utf-8">
<title>Harborline Auto – Business Card</title>
<link href="https://fonts.googleapis.com/css2?family=Poppins:wght@400;500;600;700&display=swap" rel="stylesheet">
<style>
  :root {
    --backdrop: #2b2b2b;
    --blue: #1f73a6;
    --gold: #dba43c;
    --ink: #2a2a2a;
    --rule: #c9c9c9;
  }
  * { margin: 0; padding: 0; box-sizing: border-box; }
  html, body { width: 1200px; height: 1138px; overflow: hidden; }
  body {
    background: var(--backdrop);
    font-family: "Poppins", sans-serif;
    color: var(--ink);
    position: relative;
  }
  .card {
    position: absolute;
    width: 620px;
    height: 375px;
    background: linear-gradient(135deg, #f6f6f6, #e9e9e9);
    border-radius: 14px;
    overflow: hidden;
    box-shadow: 0 6px 14px rgba(0,0,0,.45);
  }
  .card--front { left: 274px; top: 186px; }
  .card--back { left: 276px; top: 608px; }

  .brand {
    position: absolute;
    display: flex;
    align-items: center;
    gap: 12px;
    font-weight: 700;
    color: var(--blue);
    letter-spacing: .5px;
    white-space: nowrap;
  }
  .brand__dot { border-radius: 50%; background: var(--gold); flex: none; }
  .card--front .brand { left: 0; right: 0; top: 200px; justify-content: center; font-size: 30px; }
  .card--front .brand__dot { width: 22px; height: 22px; }
  .card--back .brand { right: 34px; top: 168px; font-size: 24px; }
  .card--back .brand__dot { width: 18px; height: 18px; }

  .front-web {
    position: absolute;
    left: 0; right: 0; top: 320px;
    display: flex; align-items: center; justify-content: center; gap: 22px;
    font-size: 15px;
  }
  .front-web__line { width: 52px; height: 2px; background: var(--gold); }
  .front-band {
    position: absolute; left: 0; right: 0; bottom: 0; height: 18px;
    background: linear-gradient(90deg, var(--blue) 0 50%, var(--gold) 50% 100%);
  }

  .person {
    position: absolute; left: 26px; right: 28px; top: 270px;
    display: flex; align-items: baseline; gap: 8px;
  }
  .person__name { font-size: 20px; font-weight: 700; color: var(--blue); }
  .person__title { font-size: 13.5px; }
  .person__rule { flex: 1; height: 1px; background: var(--rule); margin-left: 6px; align-self: center; }

  .contacts {
    position: absolute; left: 28px; top: 306px;
    display: grid;
    grid-template-columns: 128px 266px auto;
    row-gap: 4px;
    font-size: 12px;
  }
  .contact { display: flex; align-items: center; gap: 8px; white-space: nowrap; }
  .contact svg { width: 13px; height: 13px; flex: none; }
  .contact--phone { font-weight: 600; color: var(--blue); font-size: 13px; }
</style>
</head>
<body>

<section class="card card--front">
  <div class="brand"><span class="brand__dot"></span>HARBORLINE AUTO</div>
  <div class="front-web">
    <span class="front-web__line"></span>
    <span>www.harborlineautoxq.net</span>
    <span class="front-web__line"></span>
  </div>
  <div class="front-band"></div>
</section>

<section class="card card--back">
  <div class="brand"><span class="brand__dot"></span>HARBORLINE AUTO</div>

  <div class="person">
    <span class="person__name">DARREN HOLLOWAY</span>
    <span class="person__title">Managing Director</span>
    <span class="person__rule"></span>
  </div>

  <div class="contacts">
    <div class="contact contact--phone">
      <svg viewBox="0 0 16 16" fill="none" stroke="#dba43c" stroke-width="1.4"><circle cx="8" cy="8" r="7"/><path d="M5.5 4.5l1.5 2-1 1a5 5 0 002.5 2.5l1-1 2 1.5-1 1.5c-3 0-6-3-6-6z"/></svg>
      503-555-0148
    </div>
    <div class="contact">
      <svg viewBox="0 0 16 16" fill="none" stroke="#dba43c" stroke-width="1.3"><rect x="1.5" y="3.5" width="13" height="9" rx="1"/><path d="M1.5 4l6.5 5 6.5-5"/></svg>
      www.harborlineautoxq.net
    </div>
    <div class="contact">
      <svg viewBox="0 0 16 16" fill="none" stroke="#dba43c" stroke-width="1.3"><rect x="1.5" y="3.5" width="13" height="9" rx="1"/><path d="M1.5 4l6.5 5 6.5-5"/></svg>
      2874 Cresthaven Road,
    </div>
    <div class="contact contact--phone">
      <svg viewBox="0 0 16 16" fill="none" stroke="#dba43c" stroke-width="1.4"><circle cx="8" cy="8" r="7"/><path d="M5.5 4.5l1.5 2-1 1a5 5 0 002.5 2.5l1-1 2 1.5-1 1.5c-3 0-6-3-6-6z"/></svg>
      971-555-0173
    </div>
    <div class="contact">
      <svg viewBox="0 0 16 16" fill="none" stroke="#dba43c" stroke-width="1.3"><circle cx="8" cy="8" r="7"/><path d="M1 8h14M8 1c3 3 3 11 0 14M8 1c-3 3-3 11 0 14"/></svg>
      harborlineautoxq@mailnest.example
    </div>
    <div class="contact">
      <svg viewBox="0 0 16 16" fill="none" stroke="#dba43c" stroke-width="1.3"><circle cx="8" cy="8" r="7"/><path d="M1 8h14M8 1c3 3 3 11 0 14M8 1c-3 3-3 11 0 14"/></svg>
      Marlowe Bend, OR 97418
    </div>
  </div>
</section>

</body>
</html>
```